Maris Dovey Studio Business Cards

Hi - using the information and logo provided I require a two sided business card designed with the following information. The business card is a 'mini card' 3.5" x 1.25".

Front of card should be the logo attached but inverted (so the background is the peach colour and the logo white).

Back should have these details. If we can't fit the Pictogrum and Friendwall part can we just put the little logos.

Tessa Varnold

Art and Design Consultant
Dealer - Curator - Events - Styling - Creative Sourcing

P: 0438 217 604
E: tessa@marisdoveystudio.example
W: www.marisdoveystudio.example
I (pictogram image please): marisdoveystudio F (Friendwall image please): MarisDoveyAdviser

Target Market(s)

Galleries, artists, art buyers, interior design clients, event managers, creative types

Industry/Entity Type

Business

```html
<!DOCTYPE html>
<html lang="en">
<head>
<meta charset="utf-8">
<title>Maris Dovey Studio – Mini Business Cards</title>
<link rel="stylesheet" href="https://fonts.googleapis.com/css2?family=Arimo:wght@400&family=Cormorant+Garamond:wght@500&display=swap">
<style>
  :root {
    --backdrop: #2b2b2d;
    --peach: #e8b29a;
    --peach-deep: #d99f86;
    --peach-text: #e0a488;
    --card-white: #ffffff;
    --ink: #3a3a3a;
    --ink-soft: #555555;
    --square-blue: #3b5a99;
    --square-dark: #5a4a3e;
  }
  * { margin: 0; padding: 0; box-sizing: border-box; }
  html, body {
    width: 1200px; height: 900px; overflow: hidden;
    background: var(--backdrop);
    font-family: "Arimo", Arial, sans-serif;
  }
  .stage { position: relative; width: 1200px; height: 900px; }
  .card {
    position: absolute; left: 250px;
    width: 700px; height: 250px;
    box-shadow: 0 14px 30px rgba(0,0,0,.45);
  }
  .card--front {
    top: 150px;
    background: linear-gradient(135deg, var(--peach) 0%, var(--peach-deep) 100%);
    display: flex; align-items: center; justify-content: center;
  }
  .brand-mark {
    display: flex; align-items: center; gap: 16px;
    font-family: "Cormorant Garamond", Georgia, serif;
    font-weight: 500; font-size: 34px; letter-spacing: 1px;
  }
  .brand-mark__dot { width: 18px; height: 18px; border-radius: 50%; }
  .card--front .brand-mark { color: var(--card-white); }
  .card--front .brand-mark__dot { background: var(--card-white); }

  .card--back { top: 480px; background: var(--card-white); color: var(--ink); }
  .card--back .brand-mark {
    position: absolute; right: 28px; top: 26px;
    color: var(--peach-text); font-size: 22px; gap: 10px;
  }
  .card--back .brand-mark__dot { background: var(--peach-text); width: 12px; height: 12px; }
  .rule {
    position: absolute; left: 34px; top: 64px; width: 420px; height: 2px;
    background: var(--peach-text);
  }
  .person { position: absolute; left: 34px; top: 28px; }
  .person__name { font-size: 30px; line-height: 1; color: var(--ink); }
  .person__role { position: absolute; left: 34px; top: 74px; font-size: 15px; line-height: 1.25; color: var(--ink-soft); }
  .contacts { position: absolute; left: 34px; top: 128px; font-size: 11px; line-height: 1.55; color: var(--ink-soft); list-style: none; }
  .contacts__label { color: var(--peach-text); margin-right: 4px; }
  .social { position: absolute; display: flex; align-items: center; gap: 10px; font-size: 16px; color: var(--ink-soft); }
  .social--pictogrum { left: 34px; top: 204px; }
  .social--friendwall { left: 320px; top: 150px; }
  .social__square { width: 24px; height: 24px; border-radius: 3px; }
  .social--pictogrum .social__square { background: var(--square-dark); }
  .social--friendwall .social__square { background: var(--square-blue); }
</style>
</head>
<body>
<main class="stage">
  <section class="card card--front" aria-label="Card front">
    <div class="brand-mark"><span class="brand-mark__dot"></span>Maris Dovey Studio</div>
  </section>

  <section class="card card--back" aria-label="Card back">
    <div class="brand-mark"><span class="brand-mark__dot"></span>Maris Dovey Studio</div>
    <div class="person"><h1 class="person__name">Tessa Varnold</h1></div>
    <div class="rule"></div>
    <p class="person__role">Art and Design Consultant<br>Dealer - Curator - Events - Styling - Creative Sourcing</p>
    <ul class="contacts">
      <li><span class="contacts__label">P:</span>0438 217 604</li>
      <li><span class="contacts__label">E:</span>tessa@marisdoveystudio.example</li>
      <li><span class="contacts__label">W:</span>www.marisdoveystudio.example</li>
    </ul>
    <div class="social social--friendwall"><span class="social__square" aria-label="Friendwall"></span>MarisDoveyAdviser</div>
    <div class="social social--pictogrum"><span class="social__square" aria-label="Pictogrum"></span>marisdoveystudio</div>
  </section>
</main>
</body>
</html>
```